Patent Law

Need to develop a home page for a patent lawyer.

Colors should go with logo, blues...

Company Name- Velun Tresk, PLLC

Company Overview-

I am an Intellectual Property Lawyer and focus on patents, copyrights, trademarks, & trade secrets. I work with small businesses and start ups in the chemical and biotech industries.

Why Us-

I am small firm that can provide large-firm service at a reasonable price. I also can charge flat-fees for entreprenuers in certain practice areas.

Services-
Intellectual Property
Patents
Copyrights
Trademarks
Trade secrets
Healthcare Compliance
Elder law
Wills
Trusts

Website we like-
http://www.quorvantlegal.example/ - within industry!!
http://www.daltrowemiko.example/
http://ulbrixtane.example/
http://thegravelcounsel.example/

Target Market(s)

My customers will be small business, specifically small start-up companies in the chemical and biotech arena.

Industry/Entity Type

Trade

Requirements
Must have
• Colors should go with logo, blues...

```html
<!DOCTYPE html>
<html lang="en">
<head>
<meta charset="utf-8">
<title>Velun Tresk, PLLC — Home</title>
<link rel="stylesheet" href="https://fonts.googleapis.com/css2?family=Gelasio:wght@400;500&family=Lato:wght@400;700&family=Arimo:wght@400&display=swap">
<style>
  :root {
    --navy: #1f2a78;
    --navy-deep: #182264;
    --navy-light: #3a4699;
    --ink: #333333;
    --muted: #555555;
    --rule: #d9d9d9;
    --page-bg: #f2f2f2;
    --white: #ffffff;
    --icon-grey: #b5b5b5;
  }
  * { margin: 0; padding: 0; box-sizing: border-box; }
  html, body { width: 1200px; height: 936px; overflow: hidden; background: var(--page-bg); }
  body { position: relative; font-family: "Lato", sans-serif; color: var(--ink); }

  .page { position: absolute; left: 139px; top: 0; width: 922px; height: 936px; background: var(--white); }

  .topbar-icons { position: absolute; left: 591px; top: 4px; display: flex; gap: 7px; }
  .topbar-icons span { width: 20px; height: 20px; border-radius: 50%; background: var(--icon-grey); display: block; }

  .topbar-contact {
    position: absolute; left: 727px; top: 0; width: 235px; height: 27px;
    background: var(--navy); color: var(--white);
    display: flex; align-items: center; gap: 5px; padding-left: 11px;
    font-size: 12px; letter-spacing: 0.2px; white-space: nowrap;
  }
  .topbar-contact svg { flex: none; }
  .topbar-contact .phone { margin-left: 4px; }

  .brand { position: absolute; left: 240px; top: 48px; width: 140px; text-align: left; }
  .brand-mark { width: 34px; height: 34px; border-radius: 50%; background: var(--navy); margin: 0 0 10px 38px; }
  .brand-name { font-family: "Gelasio", serif; font-size: 12px; color: var(--navy-deep); letter-spacing: 0.5px; white-space: nowrap; }

  .main-nav { position: absolute; left: 465px; top: 49px; height: 67px; display: flex; font-family: "Gelasio", serif; font-size: 12px; letter-spacing: 0.4px; }
  .main-nav a { color: var(--ink); text-decoration: none; display: flex; align-items: center; justify-content: center; position: relative; height: 67px; white-space: nowrap; }
  .main-nav a.is-active { background: linear-gradient(var(--navy-light), var(--navy)); color: var(--white); width: 68px; }
  .main-nav a .caret { position: absolute; left: 0; right: 0; top: 42px; text-align: center; font-size: 8px; line-height: 8px; color: #777; }
  .main-nav .sep { width: 1px; height: 63px; background: var(--rule); margin-top: 3px; }

  .header-rule { position: absolute; left: 240px; top: 142px; width: 714px; height: 1px; background: #9a9a9a; }

  .hero { position: absolute; left: 240px; top: 166px; width: 714px; height: 367px; border: 2px solid #eeeeee; }
  .hero-photo { position: absolute; inset: 0; background: radial-gradient(ellipse at 60% 45%, #a9a9a9 0%, #8a8a8a 35%, #d9d9d9 70%, #f3f3f3 100%); }
  .hero-caption {
    position: absolute; left: 0; right: 0; bottom: 0; height: 55px;
    background: linear-gradient(#3a3a3a, #262626); opacity: 0.94;
    color: var(--white); font-family: "Gelasio", serif; font-size: 26px; letter-spacing: 1.2px;
    display: flex; align-items: center; justify-content: center;
  }
  .hero-arrow { position: absolute; width: 29px; height: 29px; background: #0d0d0d; display: flex; align-items: center; justify-content: center; }
  .hero-arrow.prev { left: 0; bottom: 11px; }
  .hero-arrow.next { right: 0; bottom: 19px; }

  .features { position: absolute; left: 240px; top: 557px; width: 714px; height: 285px; border: 2px solid #eeeeee; display: flex; padding: 18px 0; }
  .feature { flex: 1; text-align: center; padding-top: 66px; }
  .feature + .feature { border-left: 1px solid var(--rule); }
  .feature h2 { font-family: "Gelasio", serif; font-weight: 400; font-size: 22px; color: var(--navy-deep); letter-spacing: 0.5px; margin-bottom: 10px; }
  .feature p, .feature li { font-size: 10px; line-height: 13.5px; color: var(--muted); }
  .feature ul { list-style: none; }
  .why p { font-family: "Arimo", sans-serif; color: #222; padding: 0 16px; }
  .btn-more { display: inline-block; margin-top: 15px; width: 56px; height: 29px; line-height: 29px; background: var(--navy); color: var(--white); font-family: "Gelasio", serif; font-size: 11px; text-decoration: none; }

  .site-footer {
    position: absolute; left: 240px; top: 862px; width: 714px; height: 72px;
    background: linear-gradient(var(--navy-deep), var(--navy-light));
    color: var(--white); font-family: "Gelasio", serif; font-size: 10px; letter-spacing: 0.3px;
    text-align: center; padding-top: 24px; line-height: 14px;
  }
  .site-footer nav a { color: var(--white); text-decoration: none; margin: 0 6px; }
</style>
</head>
<body>
  <div class="page"></div>

  <div class="topbar-icons" aria-hidden="true"><span></span><span></span><span></span><span></span><span></span></div>
  <div class="topbar-contact">
    <svg width="9" height="12" viewBox="0 0 9 12"><path d="M4.5 0A4.5 4.5 0 0 0 0 4.5C0 8 4.5 12 4.5 12S9 8 9 4.5A4.5 4.5 0 0 0 4.5 0Zm0 6.3a1.8 1.8 0 1 1 0-3.6 1.8 1.8 0 0 1 0 3.6Z" fill="#fff"/></svg>
    <span>Our Map Location</span>
    <svg class="phone" width="16" height="16" viewBox="0 0 16 16"><circle cx="8" cy="8" r="7" fill="none" stroke="#fff" stroke-width="1.3"/><path d="M5.6 4.2l1.2 1.6-.7 1c.5 1 1.2 1.7 2.1 2.1l1-.7 1.6 1.2-.7 1.5c-2.6-.3-4.8-2.5-5.1-5.1Z" fill="#fff"/></svg>
    <span>555 014 2867</span>
  </div>

  <div class="brand">
    <div class="brand-mark"></div>
    <div class="brand-name">VELUN TRESK, PLLC</div>
  </div>

  <nav class="main-nav">
    <a href="#" class="is-active">HOME</a>
    <a href="#" style="width:100px">ABOUT US<span class="caret">&#8964;</span></a>
    <span class="sep"></span>
    <a href="#" style="width:130px">PRACTICE AREA<span class="caret">&#8964;</span></a>
    <span class="sep"></span>
    <a href="#" style="width:92px">LAWYERS<span class="caret">&#8964;</span></a>
    <span class="sep"></span>
    <a href="#" style="width:95px">CONTACT US</a>
  </nav>

  <div class="header-rule"></div>

  <section class="hero">
    <div class="hero-photo" role="img" aria-label="Black and white portrait photograph of a thoughtful grey-haired man"></div>
    <div class="hero-caption">WE PROVIDE LEGAL HELP FOR YOU</div>
    <a class="hero-arrow prev" href="#" aria-label="Previous slide"><svg width="10" height="16" viewBox="0 0 10 16"><path d="M8 1L2 8l6 7" fill="none" stroke="#fff" stroke-width="1.2"/></svg></a>
    <a class="hero-arrow next" href="#" aria-label="Next slide"><svg width="10" height="16" viewBox="0 0 10 16"><path d="M2 1l6 7-6 7" fill="none" stroke="#fff" stroke-width="1.2"/></svg></a>
  </section>

  <section class="features">
    <div class="feature why">
      <h2>WHY US?</h2>
      <p>Lorem ipsum dolor sit amet, consectetuer adipiscing elit, sed diam nonummy nibh euis-mod tincidunt ut laoreet dolore magna aliquam erat volutpat. Ut wisi enim ad minim veniam, quis nostrud exerci...</p>
      <a class="btn-more" href="#">More</a>
    </div>
    <div class="feature services">
      <h2>WHAT WE DO?</h2>
      <ul>
        <li>Intellectual Property</li>
        <li>Patents</li>
        <li>Copyrights</li>
        <li>Trademarks</li>
        <li>Trade secrets</li>
        <li>Healthcare Compliance</li>
        <li>Elder law</li>
        <li>Wills</li>
        <li>Trusts</li>
      </ul>
    </div>
    <div class="feature contact">
      <h2>CONTACT&nbsp; INFO</h2>
      <p>Address: Orlen Street . QX 417&nbsp; Hollis,NY<br>Phone: 4817 203 56<br>Fax: 48172 035 69</p>
    </div>
  </section>

  <footer class="site-footer">
    <p>Copyrights 2014.Velun Tresk, PLLC, All Rights Reserved.</p>
    <nav><a href="#">Home</a>|<a href="#">About Us</a>|<a href="#">Practice Area</a>|<a href="#">Lawyers</a>|<a href="#">Contact Us</a></nav>
  </footer>
</body>
</html>
```